Satchel & Sundial needs new business card design

I need a new business card design. I'm looking for out-of-the-box design which represents the freedom of being a location independent entrepreneur.
I offer coaching, retreats and trips.
I would like to see designs with and without the photo.
Colors I use are black (#000000), green (#25A796) and brown (#D7C38C)
Website satchelandsundial.example

Target Market(s)

location independent entrepreneurs, digital nomads, people looking to swap the 9 to 5 for a lifestyle business

Industry/Entity Type

Business

Contact Information for Business Card

Dorota Falkner
Your Lifestyle Business Coach, Retreat & Trip Leader
http://satchelandsundial.example
hello@satchelandsundial.example
Live a life you don't need a holiday from

Font styles to use
Serif
Sans Serif

Requirements
Must have
• One side should contain only the logo. I would also consider having the "Live a life you don't need a holiday from" on that side too (depending on how it looks)
• Please show both sides on the designs.

```html
<!DOCTYPE html>
<html lang="en">
<head>
<meta charset="utf-8">
<title>Satchel &amp; Sundial — Business Card</title>
<link rel="stylesheet" href="https://fonts.googleapis.com/css2?family=Source+Sans+3:ital,wght@0,400;0,600;0,700;1,400&display=swap">
<style>
  :root {
    --teal: #25a796;
    --ink: #231f20;
    --paper: #ffffff;
    --backdrop: #e6e6e6;
    --type: "Source Sans 3", Arial, sans-serif;
  }
  * { box-sizing: border-box; margin: 0; padding: 0; }
  html, body {
    width: 1105px; height: 1200px; overflow: hidden;
    background: var(--backdrop);
    font-family: var(--type);
  }
  .card {
    position: absolute; left: 192px;
    width: 721px; height: 413px;
    overflow: hidden;
  }
  .card--front { top: 145px; display: flex; background: var(--paper); }
  .card--back { top: 602px; background: var(--teal); }

  .front-details {
    width: 351px; height: 100%;
    background: var(--ink);
    padding: 130px 0 0 30px;
    color: var(--paper);
  }
  .holder-name {
    color: var(--teal);
    font-weight: 600; font-size: 25px;
    letter-spacing: 0.5px; text-transform: uppercase;
    line-height: 1.15;
  }
  .holder-role { font-size: 19px; line-height: 1.4; margin-top: 4px; }
  .contact-list { list-style: none; margin-top: 14px; }
  .contact-list li {
    display: flex; align-items: center; gap: 9px;
    font-size: 18px; line-height: 1.5;
  }
  .contact-icon { width: 16px; height: 16px; flex: none; }

  .front-brand {
    flex: 1; display: flex; align-items: center; justify-content: center;
  }
  .brand-name {
    font-weight: 600; font-size: 33px; color: var(--ink);
    letter-spacing: 0.5px;
  }
  .edge-strip { width: 18px; height: 100%; background: var(--teal); }

  .back-texture { position: absolute; inset: 0; background: var(--teal); }
  .social-row {
    position: absolute; top: 23px; right: 23px;
    display: flex; gap: 7px;
  }
  .social-row span { width: 24px; height: 24px; background: var(--paper); }
  .back-brand {
    position: absolute; left: 0; right: 0; top: 170px;
    text-align: center;
    font-weight: 600; font-size: 62px; color: var(--paper);
    letter-spacing: 1px;
  }
  .tagline {
    position: absolute; left: 0; right: 0; top: 350px;
    text-align: center;
    font-style: italic; font-size: 19px; color: var(--paper);
  }
</style>
</head>
<body>

<section class="card card--front" aria-label="Card front">
  <div class="front-details">
    <h1 class="holder-name">Dorota Falkner</h1>
    <p class="holder-role">Your Lifestyle Business Coach<br>Retreat &amp; Trip Leader</p>
    <ul class="contact-list">
      <li>
        <svg class="contact-icon" viewBox="0 0 16 16" aria-hidden="true">
          <rect x="1" y="3" width="14" height="10" fill="#25a796"/>
          <path d="M1 3 L8 9 L15 3" fill="none" stroke="#231f20" stroke-width="1.4"/>
        </svg>
        hello@satchelandsundial.example
      </li>
      <li>
        <svg class="contact-icon" viewBox="0 0 16 16" aria-hidden="true">
          <circle cx="8" cy="8" r="7" fill="#25a796"/>
          <path d="M1 8 H15 M8 1 C4 5 4 11 8 15 M8 1 C12 5 12 11 8 15" fill="none" stroke="#231f20" stroke-width="1"/>
        </svg>
        www.satchelandsundial.example
      </li>
    </ul>
  </div>
  <div class="front-brand">
    <p class="brand-name">Satchel &amp; Sundial</p>
  </div>
  <div class="edge-strip"></div>
</section>

<section class="card card--back" aria-label="Card back">
  <div class="back-texture" role="img" aria-label="Faint repeated brand lettering texture across the teal background"></div>
  <div class="social-row" aria-hidden="true"><span></span><span></span><span></span></div>
  <p class="back-brand">Satchel &amp; Sundial</p>
  <p class="tagline">Live a life you don't need a holiday from</p>
</section>

</body>
</html>
```